Letterhead Design for Law Firm

**Edit: I have added the photo of a bottom that I like.

------
We are looking for a re-design of our new letterhead. The letterhead is for a law firm and will be used for digital and traditionally printed correspondence.

Here are some suggestions:

- Please use colours are #8ec900 and simple black.
- Please do not use any type of "waves" at the bottom of the page. This is not in style at all.
- Please stay modern yet conservative.
- Please use font Segoe UI Light or similar if you can
- Avoid clipart or illustrations.
- Utilize ample white space in the layout so the design looks clean and information is easy to read at a glance. Don't overcrowd the letterhead.
- Make sure the letterhead design is consistent with our brand identity (see corvelith.ca)
-Please, no black headers or footers.

I am attaching my current letterhead and signature for your convenience.

Remember, the letterhead is an extension of our professional identity. We are a successful firm and trial lawyers who correspond with insurers, judges, lawyers, courts, clients, etc. Make it new, modern, attractive, yet powerful and conservative.

It needs to be easily printable. I would like the bleed removed in print so the black bar the bottom crosses the page (but the text is not near the edges)
Updates

Low design quality

Target Market(s)

Clients, Government Offices, Judiciary, Lawyers, Insurance Companies, Colleagues.

Industry/Entity Type

Law

Other font styles liked:
• Segoe UI LIght, Calibri Light,

Colors
00AB8E
00BBA5
67D7C9
C6EFE9
E9F9F6

Requirements
Must have
• Everything that is on the letterhead now.
Nice to have
• Cutting Edge design, yet conservative.
Should not have
• law firm cliche design, images,

```html
<!DOCTYPE html>
<html lang="en">
<head>
<meta charset="utf-8">
<title>Verhoeven Personal Injury Lawyers – Letterhead</title>
<link href="https://fonts.googleapis.com/css2?family=Arimo:wght@400;700&family=Mulish:wght@700&display=swap" rel="stylesheet">
<style>
  :root {
    --brand-green: #8ec900;
    --ink: #111111;
    --text-grey: #5a5a5a;
    --page-bg: #e4e4e4;
    --paper: #ffffff;
  }
  * { margin: 0; padding: 0; box-sizing: border-box; }
  html, body { width: 1189px; height: 1200px; overflow: hidden; }
  body { background: var(--page-bg); font-family: "Arimo", Arial, sans-serif; }

  .letterhead {
    position: absolute; left: 184px; top: 20px;
    width: 820px; height: 1160px;
    background: var(--paper);
    box-shadow: 3px 4px 8px rgba(0,0,0,0.18);
  }
  .rule { position: absolute; height: 1px; background: var(--brand-green); }
  .rule--top-left { left: 0; width: 66px; top: 55px; }
  .rule--top-right { left: 325px; right: 0; top: 55px; }
  .rule--bottom-left { left: 0; width: 66px; top: 116px; }
  .rule--bottom-right { left: 325px; right: 0; top: 116px; }
  .rule--logo-top { left: 73px; width: 247px; top: 55px; }
  .rule--logo-bottom { left: 73px; width: 247px; top: 116px; }

  .firm-name {
    position: absolute; left: 73px; width: 247px; top: 58px;
    text-align: center; color: var(--ink); font-weight: 400;
  }
  .firm-name__main { display: block; font-size: 44px; line-height: 56px; letter-spacing: 0.5px; }
  .firm-name__tag { display: block; font-size: 12.5px; letter-spacing: 1.6px; margin-top: 4px; }

  .contact {
    position: absolute; top: 63px; font-size: 12.6px; line-height: 15.7px; color: var(--text-grey);
  }
  .contact--digital { left: 381px; }
  .contact--address { left: 564px; }
  .contact__item { display: flex; align-items: center; gap: 4px; }
  .contact__icon { width: 9px; height: 9px; margin-left: -14px; margin-right: 4px; flex: none; }
  .contact--digital .contact__item { margin-left: 14px; }

  .salutation {
    position: absolute; left: 74px; top: 361px;
    font-family: "Mulish", sans-serif; font-weight: 700; font-size: 18.5px; color: #4a4a4a;
  }
  .letter-body {
    position: absolute; left: 73px; top: 405px; width: 676px;
    font-size: 13.4px; line-height: 17px; color: var(--text-grey);
  }
  .letter-body p { margin-bottom: 15px; }
  .closing {
    position: absolute; left: 74px; top: 760px;
    font-family: "Mulish", sans-serif; font-weight: 700; font-size: 10.5px; color: #4a4a4a;
  }
  .signature {
    position: absolute; left: 487px; top: 857px; width: 248px; height: 60px;
    background: linear-gradient(180deg, #ffffff 0%, #f0f0f0 50%, #ffffff 100%);
  }
  .signatory { position: absolute; left: 487px; top: 932px; font-size: 12.4px; line-height: 15.5px; }
  .signatory__name { color: var(--brand-green); font-weight: 700; }
  .signatory__firm { color: var(--text-grey); }
</style>
</head>
<body>
  <main class="letterhead">
    <div class="rule rule--top-left"></div>
    <div class="rule rule--top-right"></div>
    <div class="rule rule--bottom-left"></div>
    <div class="rule rule--bottom-right"></div>
    <div class="rule rule--logo-top"></div>

    <div class="firm-name">
      <span class="firm-name__main">VERHOEVEN</span>
      <span class="firm-name__tag">PERSONAL INJURY LAWYERS</span>
    </div>

    <div class="contact contact--digital">
      <div class="contact__item">
        <svg class="contact__icon" viewBox="0 0 10 10"><path d="M2 0.8 L3.6 2.8 L2.7 3.9 Q3.7 6 6.1 7.3 L7.2 6.4 L9.2 8 L8 9.4 Q3.6 9 0.6 2.2 Z" fill="var(--brand-green)"/></svg>
        905-555-0142
      </div>
      <div class="contact__item">
        <svg class="contact__icon" viewBox="0 0 10 10"><rect x="0.5" y="2" width="9" height="6.4" fill="var(--brand-green)"/><path d="M0.8 2.3 L5 5.6 L9.2 2.3" stroke="#fff" stroke-width="0.9" fill="none"/></svg>
        info@corvelith.ca
      </div>
      <div class="contact__item">
        <svg class="contact__icon" viewBox="0 0 10 10"><circle cx="5" cy="5" r="4.6" fill="var(--brand-green)"/><path d="M0.6 5 H9.4 M5 0.5 V9.5 M5 0.5 Q2.4 5 5 9.5 M5 0.5 Q7.6 5 5 9.5" stroke="#fff" stroke-width="0.7" fill="none"/></svg>
        www.corvelith.ca
      </div>
    </div>

    <div class="contact contact--address">
      <div>40 Harbour Street West</div>
      <div>Suite 1210</div>
      <div>Hamilton, ON L8P 2K6, Canada</div>
    </div>

    <h1 class="salutation">Dear Mr. Ashford,</h1>

    <section class="letter-body">
      <p>Lorem ipsum dolor sit amet, consectetuer adipiscing elit, sed diam nonmmy nibh euismod tincidunt ut laor eet dolore magna aliquam erat volutpat. Ut wisi enim ad minim veniam, quis nostrud exerci tationmcorper suscipit lobortis nisl ut aliquip ex ea commodo consequat. Duis autem vel eum iriure dolor in hendrerit in vulputate velit esse molestie consequat, vel illum dolore eu feugiat</p>
      <p>Rorem ipsum dolor sit amet, consectetuer adipiscing elit, sed diam nonmmy nibh euismod tincidunt ut laor eet dolore magna aliquam erat volutpat. Ut wisi enim ad minim veniam, quis nostrud exerci tationmcorper suscipit lobortis nisl ut aliquip ex ea commodo consequat. Duis autem vel eum iriure dolor in hendrerit in vulputate velit esse molest</p>
      <p>Dorem ipsum dolor sit amet, consectetuer adipiscing elit, sed diam nonmmy nibh euismod tincidunt ut laor eet dolore magna aliquam erat volutpat. Ut wisi enim ad minim veniam, quis nostrud exerci tationmcorper suscipit lobortis nisl ut aliquip ex ea commodo consequat. Duis autem vel eum iriure dolor in hendrerit in suscipit lobortis nisl ut aliquip ex ea commodo consequat. Duis autem vel eum iriure dolor in hendrerit in vulputate velit esse molestie consequat, vel illum</p>
      <p>Sorem ipsum dolor sit amet, consectetuer adipiscing elit, sed diam nonmmy nibh euismod tincidunt ut laor eet dolore magna aliquam erat volutpat. Ut wisi enim ad minim veniam, quis nostrud exerci tationmcorper suscipit lobortis nisl ut aliquip ex ea commodo consequat. Duis autem vel eum iriure dolor in</p>
    </section>

    <p class="closing">Sincerely,</p>

    <div class="signature" role="img" aria-label="Handwritten signature of Daniel R. Verhoeven"></div>

    <div class="signatory">
      <div class="signatory__name">Daniel R. Verhoeven</div>
      <div class="signatory__firm">Verhoeven Law Professional Corporation</div>
    </div>
  </main>
</body>
</html>
```